IT Company requires new Business Card design.

Over the years we have had a few different business card designs. We are now due for new cards across the board for all staff. We felt this would be a good time to start fresh with a new design. Our traditional card simply had our details on the front, and a list of services on the back. We don't particularly need the list of services, we have had cards where the only thing on the rear of the card was our logo.
Feel free to be creative, we would like our tag line "Complete IT Management" to appear at some point, doesn't necessarily have to be with the logo.
I have attached samples and drafts of various previous cards we have used over the years.

```html
<!DOCTYPE html>
<html lang="en">
<head>
<meta charset="utf-8">
<title>Ridgeline Systems – Business Card</title>
<link href="https://fonts.googleapis.com/css2?family=Open+Sans:wght@400;600;700&display=swap" rel="stylesheet">
<style>
  :root {
    --backdrop: #e6e3df;
    --card-white: #ffffff;
    --slate: #5f727d;
    --slate-dark: #3f4b52;
    --ink: #5a6b75;
    --ink-soft: #6d7c85;
    --divider: #c9d0d4;
    --on-slate: #ffffff;
  }
  * { box-sizing: border-box; margin: 0; padding: 0; }
  html, body {
    width: 1034px; height: 1200px; overflow: hidden;
    background: var(--backdrop);
    font-family: "Open Sans", Arial, sans-serif;
  }
  .canvas { position: relative; width: 1034px; height: 1200px; }

  .card {
    position: absolute; left: 75px; width: 902px; height: 518px;
    border-radius: 34px; overflow: hidden;
    box-shadow: 0 6px 18px rgba(0,0,0,.18);
  }
  .card--front { top: 65px; background: var(--card-white); }
  .card--back { top: 626px; height: 514px; background: var(--slate); }

  .front-wave { position: absolute; left: 0; top: 0; width: 902px; height: 518px; }

  .brand {
    position: absolute; left: 85px; top: 150px;
    display: flex; align-items: center; gap: 18px;
  }
  .brand__square { width: 64px; height: 64px; background: var(--ink); }
  .brand__name {
    color: var(--ink); font-weight: 700; font-size: 38px;
    line-height: 1.02; text-transform: uppercase; letter-spacing: .5px;
  }

  .divider {
    position: absolute; left: 460px; top: 72px; width: 2px; height: 330px;
    background: var(--divider);
  }

  .contact { position: absolute; left: 482px; top: 76px; color: var(--ink); }
  .contact__name { font-size: 27px; font-weight: 700; line-height: 1.2; }
  .contact__role { font-size: 22px; color: var(--ink-soft); margin-top: 2px; }
  .contact__list { list-style: none; margin-top: 26px; }
  .contact__item {
    display: flex; align-items: center; gap: 12px;
    font-size: 21px; height: 36px;
  }
  .contact__icon { width: 20px; height: 20px; fill: var(--ink); flex: none; }

  .address {
    position: absolute; left: 78px; top: 438px;
    color: var(--on-slate); font-size: 21px; line-height: 32px;
  }

  .back-brand {
    position: absolute; left: 0; right: 0; top: 150px;
    display: flex; flex-direction: column; align-items: center; gap: 28px;
  }
  .back-brand__square { width: 120px; height: 120px; background: var(--on-slate); }
  .back-brand__name {
    color: var(--on-slate); font-weight: 700; font-size: 52px;
    text-transform: uppercase; letter-spacing: 2px;
  }
  .tagline {
    position: absolute; left: 0; right: 0; top: 448px; text-align: center;
    color: var(--on-slate); font-size: 24px; letter-spacing: 5px;
    text-transform: uppercase;
  }
</style>
</head>
<body>
<main class="canvas">

  <section class="card card--front" aria-label="Card front">
    <svg class="front-wave" viewBox="0 0 902 518" aria-hidden="true">
      <path d="M0 432 C 90 405, 170 392, 260 398 C 420 410, 520 490, 650 482 C 760 476, 840 440, 902 418 L902 518 L0 518 Z" fill="var(--slate)"/>
      <path d="M0 414 C 90 388, 170 376, 260 382 C 420 394, 520 472, 650 466 C 760 460, 840 424, 902 402 L902 410 C 840 432, 760 468, 650 474 C 520 482, 420 402, 260 390 C 170 384, 90 398, 0 424 Z" fill="var(--slate-dark)"/>
    </svg>

    <div class="brand">
      <span class="brand__square"></span>
      <span class="brand__name">Ridgeline<br>Systems</span>
    </div>

    <div class="divider"></div>

    <div class="contact">
      <p class="contact__name">Marcus Hale</p>
      <p class="contact__role">Operation Manager</p>
      <ul class="contact__list">
        <li class="contact__item">
          <svg class="contact__icon" viewBox="0 0 20 20"><path d="M5 2l3 4-2 2c1 2.5 3 4.5 5.5 5.5l2-2 4 3-2 3C9 17 3 11 2 5z"/></svg>
          08 9320 4415
        </li>
        <li class="contact__item">
          <svg class="contact__icon" viewBox="0 0 20 20"><path d="M6 1h8v18H6zM8 3v11h4V3z"/></svg>
          0412 738 096
        </li>
        <li class="contact__item">
          <svg class="contact__icon" viewBox="0 0 20 20"><path d="M5 2h10v5H5zM2 8h16v7h-3v3H5v-3H2zM7 13v3h6v-3z"/></svg>
          08 9320 4415
        </li>
        <li class="contact__item">
          <svg class="contact__icon" viewBox="0 0 20 20"><path d="M2 5h16v11H2zM3.5 6.5l6.5 5 6.5-5v-.5h-13z" fill-rule="evenodd"/></svg>
          marcus@ridgelinesystems.com.au
        </li>
        <li class="contact__item">
          <svg class="contact__icon" viewBox="0 0 20 20"><path d="M10 1a9 9 0 1 0 0 18 9 9 0 0 0 0-18zm0 2c1 1.3 1.7 3.5 1.9 6H8.1c.2-2.5.9-4.7 1.9-6zM3.1 9a7 7 0 0 1 3.6-5.2C6.3 5.2 6 7 6 9zm0 2H6c.1 2 .4 3.8 1 5.2A7 7 0 0 1 3.1 11zm5 0h3.8c-.2 2.5-.9 4.7-1.9 6-1-1.3-1.7-3.5-1.9-6zm5.8 0h2.9a7 7 0 0 1-3.9 5.2c.6-1.4 1-3.2 1-5.2zm0-2c0-2-.4-3.8-1-5.2A7 7 0 0 1 16.9 9z"/></svg>
          www.ridgelinesystems.com.au
        </li>
      </ul>
    </div>

    <address class="address" style="font-style:normal">
      Unit 7 22 Harbour Lane<br>
      Bibra Lake WA 6163
    </address>
  </section>

  <section class="card card--back" aria-label="Card back">
    <div class="back-brand">
      <span class="back-brand__square"></span>
      <span class="back-brand__name">Ridgeline Systems</span>
    </div>
    <p class="tagline">Complete IT Management</p>
  </section>

</main>
</body>
</html>
```